50 years of Beat (birthday party)

I need a flyer that I can send to all guests as ChatLoop.
Also as a digital file (e.g. PDF). Thanks!
Occasion: Beat's 50th birthday
It's a birthday party for family and friends
Location: Marquee at the sports ground, 7345 Tallwil
Live music
Bar pub
Corrabeg
Date: Saturday, May 25, 2024
Time: from 2 p.m. until open-end
Flexible participation - come and go as you please
Registration or deregistration: ChatLoop on 078 - 512 63 17

Please create a flyer as an invitation. I want an Irish rock style with a touch of “Schlager” :-). There should be a real party.
Attention: no heavy metal style!!
It would be cool if a rock guitar and/or microphone were included.
Otherwise, I'm free and happy to be surprised. The flyer should not be too childish or youthful. There are practically no children at the event.

Additionally, please send a simpler flyer than “Save the date”.
Just the date and occasion.
Without place, time and registration.
With the note: Update follows...
The design is the same as the flyer with registration.
Updates

It would be cool if the Corrabeg logo was visible too.
A whiskey glass would also be possible.
Balloons are not absolutely necessary - it looks like a children's party.
Please make the flyers rocky.

Target Market(s)

Family & Friends

Industry/Entity Type

look

Font styles to use
Other font styles liked:
• rockig

Colors

Designer to choose colors to be used in the design.

Requirements
Must have
• Irish rock design
Nice to have
• Rock guitar would be cool
Should not have
• comics

```html
<!DOCTYPE html>
<html lang="en">
<head>
<meta charset="utf-8">
<title>Beat's 50th Birthday – Invitation and Save the Date</title>
<link href="https://fonts.googleapis.com/css2?family=Archivo+Black&family=Oswald:wght@400;500;600&display=swap" rel="stylesheet">
<style>
  :root {
    --stage: #444444;
    --paper-dark: #1c1c1c;
    --paper-mid: #2a2a2a;
    --paper-light: #3c3c3c;
    --green: #3dbb4a;
    --white: #ffffff;
    --band: rgba(120, 120, 120, 0.85);
    --grid: rgba(255, 255, 255, 0.12);
  }
  * { margin: 0; padding: 0; box-sizing: border-box; }
  html, body { width: 1200px; height: 1200px; overflow: hidden; background: var(--stage); }

  .flyer-slot { position: absolute; top: 252px; width: 557px; height: 696px; }
  .flyer-slot--invite { left: 29px; }
  .flyer-slot--save { left: 614px; }

  .flyer {
    position: absolute; top: 0; left: 0;
    width: 696px; height: 870px;
    transform: scale(0.8); transform-origin: top left;
    overflow: hidden;
    background: linear-gradient(160deg, var(--paper-mid) 0%, var(--paper-dark) 45%, #232323 100%);
    color: var(--white);
    font-family: "Oswald", sans-serif;
  }

  .grid-line { position: absolute; background: var(--grid); }
  .grid-line--v1 { left: 42px; top: 0; width: 1px; height: 300px; }
  .grid-line--h1 { left: 0; top: 58px; width: 696px; height: 1px; }
  .grid-line--h2 { left: 0; top: 296px; width: 696px; height: 1px; }
  .grid-line--v2 { left: 650px; top: 0; width: 1px; height: 300px; }

  .scene-photo {
    position: absolute; left: 0; top: 290px; width: 696px; height: 390px;
    background:
      radial-gradient(ellipse 190px 230px at 520px 210px, rgba(40, 170, 60, 0.85), rgba(20, 90, 30, 0.4) 60%, transparent 80%),
      radial-gradient(ellipse 120px 150px at 270px 200px, rgba(190, 170, 150, 0.55), rgba(110, 70, 40, 0.35) 60%, transparent 85%),
      radial-gradient(ellipse 330px 120px at 200px 300px, rgba(170, 170, 175, 0.5), transparent 80%);
  }
  .guitar-neck {
    position: absolute; left: 520px; top: 0; width: 200px; height: 330px;
    background: linear-gradient(200deg, rgba(60, 140, 70, 0.45), rgba(90, 60, 60, 0.25) 60%, transparent);
    clip-path: polygon(78% 0, 100% 0, 28% 100%, 10% 100%);
  }

  .torn-paper { position: absolute; left: 0; top: 600px; width: 696px; height: 270px; }

  .title { position: absolute; left: 49px; top: 52px; font-family: "Archivo Black", sans-serif; font-size: 82px; line-height: 74px; letter-spacing: 1px; z-index: 2; }
  .title__line { display: block; white-space: nowrap; }
  .title .is-green { color: var(--green); }
  .title .is-white { color: var(--white); }

  .tagline-band {
    position: absolute; left: 42px; top: 196px; width: 482px; height: 52px;
    background: var(--band); z-index: 1;
    display: flex; align-items: center; padding-left: 19px;
    font-size: 23px; font-weight: 500; letter-spacing: 1.2px; text-transform: uppercase;
  }

  .features {
    position: absolute; left: 637px; top: 585px;
    transform: rotate(-90deg); transform-origin: left top;
    font-size: 30px; font-weight: 500; letter-spacing: 0.5px; white-space: nowrap; text-transform: uppercase;
  }

  .date-block { position: absolute; display: flex; height: 37px; }
  .date-block__day { background: var(--green); width: 130px; display: flex; align-items: center; justify-content: center; font-family: "Archivo Black", sans-serif; font-size: 21px; }
  .date-block__meta { border: 1px solid var(--green); width: 108px; padding-left: 23px; display: flex; flex-direction: column; justify-content: center; font-family: "Archivo Black", sans-serif; font-size: 12px; line-height: 12px; }

  .small-caps { position: absolute; font-size: 14px; font-weight: 500; text-transform: uppercase; line-height: 17px; }
  .info { position: absolute; text-transform: uppercase; }
  .info__label { font-size: 16px; font-weight: 500; letter-spacing: 0.3px; }
  .info__value { font-size: 24px; font-weight: 500; color: var(--green); line-height: 28px; }

  .save-heading { position: absolute; left: 49px; top: 722px; font-family: "Archivo Black", sans-serif; font-size: 56px; line-height: 54px; }
  .update-note { position: absolute; right: 48px; top: 796px; font-size: 26px; font-weight: 500; text-transform: uppercase; }
</style>
</head>
<body>

<section class="flyer-slot flyer-slot--invite">
  <article class="flyer">
    <div class="grid-line grid-line--v1"></div>
    <div class="grid-line grid-line--v2"></div>
    <div class="grid-line grid-line--h1"></div>
    <div class="grid-line grid-line--h2"></div>
    <div class="guitar-neck" role="img" aria-label="Neck of a green electric guitar"></div>
    <div class="scene-photo" role="img" aria-label="Photo of a crystal whiskey glass and a green electric guitar in drifting smoke"></div>
    <svg class="torn-paper" viewBox="0 0 696 270" aria-hidden="true">
      <polygon fill="#3a3a3a" points="0,70 60,40 120,55 180,35 240,60 300,58 350,30 400,50 450,45 520,20 600,10 650,0 696,5 696,270 0,270"/>
    </svg>

    <h1 class="title">
      <span class="title__line"><span class="is-green">BEAT'S</span> <span class="is-white">50TH</span></span>
      <span class="title__line is-green">BIRTHDAY</span>
    </h1>
    <p class="tagline-band">It's a birthday party for family and friends</p>
    <p class="features">Live music &nbsp;I&nbsp; Bar pub &nbsp;I&nbsp; Corrabeg</p>

    <div class="date-block" style="left:50px; top:677px;">
      <span class="date-block__day">May 25</span>
      <span class="date-block__meta"><span>Saturday</span><span>2024</span></span>
    </div>
    <p class="small-caps" style="left:72px; top:724px;">From 2 p.m. until open-end</p>
    <p class="small-caps" style="left:487px; top:679px;">Marquee at the sports ground,<br>7345 Tallwil</p>

    <div class="info" style="left:49px; top:778px;">
      <p class="info__label">Flexible participation</p>
      <p class="info__value">Come and go as you please</p>
    </div>
    <div class="info" style="left:385px; top:778px;">
      <p class="info__label">Registration or deregistration</p>
      <p class="info__value">ChatLoop on 078-512-63-17</p>
    </div>
  </article>
</section>

<section class="flyer-slot flyer-slot--save">
  <article class="flyer">
    <div class="grid-line grid-line--v1"></div>
    <div class="grid-line grid-line--v2"></div>
    <div class="grid-line grid-line--h1"></div>
    <div class="grid-line grid-line--h2"></div>
    <div class="guitar-neck" role="img" aria-label="Neck of a green electric guitar"></div>
    <div class="scene-photo" role="img" aria-label="Photo of a crystal whiskey glass and a green electric guitar in drifting smoke"></div>
    <svg class="torn-paper" viewBox="0 0 696 270" aria-hidden="true">
      <polygon fill="#3a3a3a" points="0,70 60,40 120,55 180,35 240,60 300,58 350,30 400,50 450,45 520,20 600,10 650,0 696,5 696,270 0,270"/>
    </svg>

    <h1 class="title">
      <span class="title__line"><span class="is-green">BEAT'S</span> <span class="is-white">50TH</span></span>
      <span class="title__line is-green">BIRTHDAY</span>
    </h1>
    <p class="tagline-band">It's a birthday party for family and friends</p>
    <p class="features">Live music &nbsp;I&nbsp; Bar pub &nbsp;I&nbsp; Corrabeg</p>

    <h2 class="save-heading">Save<br>the Date</h2>
    <div class="date-block" style="left:410px; top:745px;">
      <span class="date-block__day">May 25</span>
      <span class="date-block__meta"><span>Saturday</span><span>2024</span></span>
    </div>
    <p class="update-note">Update follows...</p>
  </article>
</section>

</body>
</html>
```